Simple, High-Class Web Design Wanted - Motivational Speakers Site

1. Full Brief/Request & Specs outlined on following video -
http://clipvault-demo.com/watch/rTkWmaPzQb

2. Use colours, images as you feel suits objective (we are happy to pay up to US$30 for any good images but must have licence/permission).

3. Layout probably similar to existing site - www.podiumtalentgroup.com.au / http://podiumtalentgroup.com.au/contact.php

4. Must Be Able to Coded for MOBILE-FRIENDLINESS & WordPress friendly Ideal.

5. This is the first, small job of many we/graphic design jobs. If suits, winning designer may be offered all future work direct.

Thanks & look forward to your design. Glen.

Target Market(s)

corporates - high end

Number of Pages Required

2 page

Font styles to use
Sans Serif

Requirements
Must have
• Classy professional look
Nice to have
• all in Video in brief
Should not have
• too many images / new images I haven't approved

```html
<!DOCTYPE html>
<html lang="en">
<head>
<meta charset="utf-8">
<title>Podium Talent Group – Find The Perfect Speaker</title>
<link href="https://fonts.googleapis.com/css2?family=Open+Sans:ital,wght@0,300;0,400;0,600;0,700;1,400&display=swap" rel="stylesheet">
<style>
:root{
  --page:#d9dadc;
  --paper:#ffffff;
  --ink:#4a4f55;
  --muted:#8a9096;
  --hero-a:#3e5560;
  --hero-b:#6f8a94;
  --teal:#3bb3a3;
  --blue:#4a9fd8;
  --blue-dark:#3a88c0;
  --green:#2fbf8f;
  --video-bg:#eceeef;
  --footer:#2d3338;
  --rule:#e1e4e6;
}
*{box-sizing:border-box;margin:0;padding:0}
html,body{width:730px;height:1200px;overflow:hidden}
body{background:var(--page);font-family:"Open Sans",Arial,sans-serif;color:var(--ink)}
.page{position:absolute;left:58px;top:0;width:614px;height:1185px;background:var(--paper)}
.hero{position:relative;height:220px;background:linear-gradient(160deg,var(--hero-a),var(--hero-b) 60%,#8fa5ad);color:#fff;padding:30px 34px}
.hero h1{font-size:22px;font-weight:600;line-height:1.2;letter-spacing:.2px}
.hero .sub{font-size:17px;font-weight:300;margin-top:2px}
.hero .rule{position:absolute;left:34px;top:92px;width:220px;border-top:1px solid rgba(255,255,255,.6)}
.hero .pitch{position:absolute;right:40px;top:110px;width:250px;font-size:12px;font-style:italic;line-height:1.4}
.hero .details{position:absolute;right:40px;top:190px;background:var(--teal);font-size:8px;font-weight:600;padding:4px 12px;border-radius:2px;letter-spacing:.5px}
.video-band{background:var(--video-bg);height:295px;padding-top:18px}
.player{width:290px;height:225px;margin:0 auto;background:#fff;padding:8px;box-shadow:0 1px 3px rgba(0,0,0,.15);position:relative}
.player .frame{width:100%;height:100%;background:linear-gradient(180deg,#c9d2d8,#8da3b3 60%,#6f879b)}
.player .play{position:absolute;left:50%;top:50%;transform:translate(-50%,-50%)}
.player .controls{position:absolute;left:14px;bottom:14px;display:flex;gap:4px}
.player .controls i{width:9px;height:9px;border-radius:50%;background:rgba(255,255,255,.7)}
.cta-blue{display:block;width:230px;margin:16px auto 0;background:var(--blue);color:#fff;font-size:9.5px;font-weight:600;text-align:center;padding:6px 0;border-radius:3px}
.section-title{text-align:center;font-size:20px;font-weight:300;color:var(--muted);padding-top:14px}
.section-title:after{content:"";display:block;width:440px;margin:6px auto 0;border-top:1px solid var(--rule)}
.body-copy{padding:14px 34px 0;font-size:9px;line-height:1.55;color:var(--ink)}
.body-copy p{margin-bottom:8px}
.band{margin-top:8px;background:var(--blue);color:#fff;text-align:center;padding:14px 0 16px;font-size:8.5px;line-height:2.1}
.band strong{font-weight:600}
.cta-green{display:inline-block;background:var(--green);color:#fff;font-size:8.5px;font-weight:700;padding:5px 14px;border-radius:3px;letter-spacing:.3px;margin-top:6px}
.note .body-copy{text-align:center;padding-top:16px}
.contact-bar{margin-top:20px;border-top:1px solid var(--rule);padding:16px 34px;display:flex;align-items:center;gap:14px;font-size:8.5px}
.contact-bar .cta-green{margin:0}
.contact-bar b{color:var(--blue-dark);font-weight:600}
.site-footer{position:absolute;left:0;right:0;bottom:0;height:48px;background:var(--footer);color:#b9c0c5;font-size:7.5px;text-align:center;line-height:1.5;padding-top:13px}
.site-footer .top{position:absolute;right:14px;top:-22px;width:16px;height:16px;background:var(--teal)}
</style>
</head>
<body>
<div class="page">
  <header class="hero" role="img" aria-label="Header photo of a bright modern conference room">
    <h1>Find The Perfect Speaker For Your Next Event Here...</h1>
    <div class="sub">free industry service</div>
    <div class="rule"></div>
    <p class="pitch">Looking for a top motivational or guest speaker, MC, industry expert to "WOW" your audience - find them here</p>
    <span class="details">» DETAILS</span>
  </header>

  <section class="video-band">
    <div class="player">
      <div class="frame" role="img" aria-label="Video still of the presenter introducing the service"></div>
      <svg class="play" width="34" height="34" viewBox="0 0 34 34"><circle cx="17" cy="17" r="17" fill="#2fbf8f"/><path d="M13 10l11 7-11 7z" fill="#fff"/></svg>
      <div class="controls"><i></i><i></i><i></i></div>
    </div>
    <span class="cta-blue">I Want to Make our Event a Great Success &nbsp;»</span>
  </section>

  <section class="about">
    <h2 class="section-title">About</h2>
    <div class="body-copy">
      <p>Podium Talent Group is a free industry service designed to help people looking for speakers avoid precious time and frustration in finding the most suitable best speaker for their needs.</p>
      <p>Suggestions are given by conference speaker Glen Harper, who has presented around Australia for a number of years and is familiar with many of our top professional speakers, MCs as well as the leading speaker bureaus.</p>
      <p>If you would like a hand finding some good speaker options, simply send us the details of your event and the type of presenter you are ideally after, e.g.</p>
    </div>
    <div class="band">
      <div><strong>Typical Style</strong> – Motivational, Entertaining, Keynote/Workshop, MC etc</div>
      <div><strong>Topic Style</strong> – Team Building, Leadership, Inspiration, Health/Life Balance etc</div>
      <div><strong>Approximate Budget</strong> – $1000, $3000, $5000, $7000+ etc</div>
      <div><strong>Location</strong> – Sydney, Melbourne, Brisbane, Perth, Adelaide, Canberra etc</div>
      <span class="cta-green">COMPLETE ONLINE CONTACT FORM &nbsp;»</span>
    </div>
    <div class="body-copy" style="padding-top:16px">
      <p>and where we can, we will be happy to send you some speaker possibilities/ideas, trusted speakers bureaus or simply some thoughts on the best places for you to look. Regards Glen.</p>
    </div>
  </section>

  <section class="note">
    <h2 class="section-title" style="padding-top:26px">Note</h2>
    <div class="body-copy">
      <p>Any information you provide will ONLY ever be used to help with your specific enquiry.</p>
      <p>Glen does not have any financial agreements with any individual speakers he recommends. He offers this service as it only takes a few minutes of his time, helps promote other professional speakers and obviously keeps his own name out there in the industry.</p>
      <p>Please understand that while Glen tries to respond quickly, due to his own speaking/travel commitments it may take up to 24 hours.</p>
    </div>
  </section>

  <div class="contact-bar">
    <span class="cta-green">COMPLETE ONLINE CONTACT FORM &nbsp;»</span>
    <span>E-MAIL: <b>suggestions@podiumtalentgroup.com.au</b> &nbsp;or PHONE: <b>1300 555 014</b></span>
  </div>

  <footer class="site-footer">
    <span class="top"></span>
    <div>© 2015. All Rights Reserved. www.podiumtalentgroup.com.au &nbsp;PO Box 418, Harbourview NSW 2071</div>
    <div>E-mail: suggestions@podiumtalentgroup.com.au &nbsp;Phone: 1300 555 014</div>
  </footer>
</div>
</body>
</html>
```